Real Estate Company / Capital Needs Cards!

need business cards designed using the logos that were just designed by pixelbarn.

Reason: per designers request deadline extended 1 day…thank you.

Target Market(s)

Investors and clients looking to purchase real estate or invest in the business.

Industry/Entity Type

Business

Requirements
Must have
• two designs - one for the real estate logo and one for the capital logo, similar but slightly different.
Nice to have
• something to make it pop (perhaps on the back)
Should not have
• much color

```html
<!DOCTYPE html>
<html lang="en">
<head>
<meta charset="utf-8">
<title>Corvan Real Estate – Business Cards</title>
<link href="https://fonts.googleapis.com/css2?family=Marcellus&family=Open+Sans:wght@400;600&display=swap" rel="stylesheet">
<style>
  :root {
    --page-bg: #e9e7e4;
    --card-black: #050505;
    --silver: #d8d8d8;
    --silver-light: #f2f2f2;
    --silver-dark: #9a9a9a;
    --ink-white: #f4f4f4;
    --band-text: #111111;
  }
  * { box-sizing: border-box; margin: 0; padding: 0; }
  html, body {
    width: 1200px; height: 434px; overflow: hidden;
    background: var(--page-bg);
  }
  .sheet {
    position: relative; width: 1200px; height: 434px;
    display: flex; justify-content: center; align-items: center; gap: 44px;
  }
  .card {
    position: relative; width: 540px; height: 310px;
    background: var(--card-black);
    box-shadow: 0 6px 18px rgba(0,0,0,.25);
    overflow: hidden;
  }

  .brand-name {
    font-family: "Marcellus", serif; line-height: 1; text-transform: uppercase;
    background: linear-gradient(180deg, var(--silver-light), var(--silver-dark) 55%, var(--silver));
    -webkit-background-clip: text; background-clip: text; color: transparent;
  }

  /* Front */
  .front-brand {
    position: absolute; top: 36px; left: 0; right: 0;
    display: flex; justify-content: center; align-items: center; gap: 14px;
  }
  .brand-square {
    width: 60px; height: 60px; border-radius: 6px;
    background: linear-gradient(135deg, var(--silver-light), var(--silver-dark));
  }
  .front-brand .brand-name .word { display: block; font-size: 46px; letter-spacing: 1px; }
  .front-brand .brand-name .sub { display: block; font-size: 18px; letter-spacing: 3.5px; margin-top: 2px; }

  .name-band {
    position: absolute; top: 152px; left: 0; right: 0; height: 42px;
    background: linear-gradient(90deg, var(--silver-dark), var(--silver-light) 45%, var(--silver) 70%, var(--silver-dark));
    display: flex; align-items: center; justify-content: center;
    font-family: "Open Sans", sans-serif; font-size: 18px; color: var(--band-text);
  }
  .name-band strong { font-weight: 600; }

  .contact {
    position: absolute; top: 212px; left: 0; right: 0;
    display: flex; justify-content: center; align-items: center;
    font-family: "Open Sans", sans-serif; color: var(--ink-white);
  }
  .address { font-style: normal; text-align: right; font-size: 15px; line-height: 1.45; padding-right: 12px; }
  .divider { width: 1px; height: 66px; background: var(--ink-white); }
  .lines { padding-left: 10px; font-size: 16px; line-height: 1.4; }
  .lines li { list-style: none; display: flex; align-items: center; gap: 5px; }
  .lines li.email { font-size: 15px; }
  .lines svg { width: 13px; height: 13px; fill: var(--ink-white); flex: none; }

  /* Back */
  .back-brand {
    position: absolute; top: 70px; left: 0; right: 0; text-align: center;
  }
  .back-brand .word { display: block; font-size: 92px; letter-spacing: 2px; }
  .back-brand .sub { display: block; font-size: 38px; letter-spacing: 9px; margin-top: 4px; }
  .web {
    position: absolute; bottom: 30px; left: 0; right: 0; text-align: center;
    font-family: "Open Sans", sans-serif; font-size: 17px; letter-spacing: 2px;
    color: var(--ink-white);
  }
</style>
</head>
<body>
<main class="sheet">

  <section class="card card-front" aria-label="Business card front">
    <div class="front-brand">
      <span class="brand-square" aria-hidden="true"></span>
      <span class="brand-name"><span class="word">Corvan</span><span class="sub">Real Estate</span></span>
    </div>

    <div class="name-band"><span><strong>Your Name,</strong> Title</span></div>

    <div class="contact">
      <address class="address">Street Name, City Name<br>State ZipCode</address>
      <span class="divider" aria-hidden="true"></span>
      <ul class="lines">
        <li><svg viewBox="0 0 24 24" aria-hidden="true"><path d="M6.6 10.8a15 15 0 0 0 6.6 6.6l2.2-2.2a1 1 0 0 1 1-.25 11.4 11.4 0 0 0 3.6.57 1 1 0 0 1 1 1V20a1 1 0 0 1-1 1A17 17 0 0 1 3 4a1 1 0 0 1 1-1h3.5a1 1 0 0 1 1 1c0 1.25.2 2.45.57 3.57a1 1 0 0 1-.25 1z"/></svg>123-456-7980</li>
        <li><svg viewBox="0 0 24 24" aria-hidden="true"><path d="M7 1h10a2 2 0 0 1 2 2v18a2 2 0 0 1-2 2H7a2 2 0 0 1-2-2V3a2 2 0 0 1 2-2zm0 4v13h10V5z"/></svg>123-568-7896</li>
        <li class="email"><svg viewBox="0 0 24 24" aria-hidden="true"><path d="M2 5h20v14H2zm2 2v.5l8 5 8-5V7zm0 3v7h16v-7l-8 5z"/></svg>corvanrealestate@mailbox.com</li>
      </ul>
    </div>
  </section>

  <section class="card card-back" aria-label="Business card back">
    <div class="back-brand brand-name">
      <span class="word">Corvan</span>
      <span class="sub">Real Estate</span>
    </div>
    <p class="web">www.corvanrealestate.com</p>
  </section>

</main>
</body>
</html>
```